Create a proposal + product powerpoint

Please see the powerpoint for the slides. There are about 20 slides to be created. Rest of them are for reference and show the design that I like.

I would like to move fast on this, since I need to present it next week (in the week of April 21st).

Please download the current content from here:
https://www.parcelbrook.net/fetch/qRtVmXzLwPkNbYcD

Please make at least 4 slides with the specific content so I can assess your design style.

Target Market(s)

Business Audience and very senior technical audience
Decision Makers

Industry/Entity Type

Product

Colors
e34297
a64599

Requirements
Must have
• Should be very clean, crisp.

I like to use Icons as shown in the powerpoint.... Please see the appendix of the slide deck that shows the various icons. Most of them just have plain text, and I would like to organize so that it does not look like some is just reading text.

I would like to focus on the design aspects so that the audience is clear on how the solution works.

Every page should some graphic element based on the slides shown in the appendix.

```html
<!DOCTYPE html>
<html lang="en">
<head>
<meta charset="utf-8">
<title>Framework to define lifecycle management processes</title>
<link rel="stylesheet" href="https://fonts.googleapis.com/css2?family=Roboto+Condensed:wght@400;700&display=swap">
<style>
  :root {
    --title-purple: #a0179a;
    --box-top: #a2409d;
    --box-bottom: #cd46c2;
    --connector: #f08ade;
    --rule-grey: #d4d4d4;
    --logo-grey: #9a9a9a;
    --footer-dark: #9b1f5c;
    --footer-light: #a64599;
    --accent-pink: #e34297;
    --mesh-light: #e9e9ea;
    --mesh-mid: #a9abae;
    --white: #ffffff;
  }
  * { box-sizing: border-box; margin: 0; padding: 0; }
  html, body { width: 1200px; height: 900px; overflow: hidden; background: var(--white); }
  .slide {
    position: relative; width: 1200px; height: 900px; overflow: hidden;
    font-family: "Roboto Condensed", "Arial Narrow", sans-serif;
    background: var(--white);
  }
  .backdrop-glow {
    position: absolute; inset: 0;
    background:
      radial-gradient(ellipse 260px 220px at 0 600px, rgba(214, 120, 210, 0.22), transparent 70%),
      linear-gradient(100deg, transparent 72%, rgba(227, 140, 225, 0.25) 82%, rgba(206, 90, 210, 0.65) 100%);
  }
  .slide-title {
    position: absolute; left: 40px; top: 22px;
    font-size: 39px; font-weight: 400; color: var(--title-purple);
    letter-spacing: 0.2px;
  }
  .header-rule {
    position: absolute; left: 42px; right: 0; top: 90px; height: 2px;
    background: var(--rule-grey);
  }
  .logo-slot {
    position: absolute; left: 1035px; top: 12px; width: 150px; height: 66px;
    border: 2px solid #e6e6e6; border-radius: 9px; background: var(--white);
    display: flex; align-items: center; justify-content: center;
    font-size: 27px; color: var(--logo-grey);
  }
  .mesh-photo {
    position: absolute; left: 492px; top: 230px; width: 606px; height: 403px;
    background: linear-gradient(160deg, var(--mesh-light), var(--mesh-mid) 55%, var(--mesh-light));
    border: 4px solid var(--white);
  }
  .connectors { position: absolute; left: 0; top: 0; }
  .stage-box {
    position: absolute; width: 117px; height: 112px;
    background: linear-gradient(180deg, var(--box-top), var(--box-bottom));
    color: var(--white); font-weight: 700;
    display: flex; align-items: center; justify-content: center;
  }
  .stage-box.qa { font-size: 50px; height: 113px; }
  .stage-box.dev { height: 108px; align-items: baseline; padding-top: 30px; }
  .dev-label { font-size: 26px; }
  .dev-number { font-size: 46px; margin-left: 2px; }
  .footer { position: absolute; left: 0; top: 843px; width: 1200px; height: 57px; }
  .footer-shapes { position: absolute; inset: 0; }
  .page-number, .copyright {
    position: absolute; top: 12px; font-size: 25px; color: var(--white);
  }
  .page-number { left: 15px; }
  .copyright { right: 15px; }
</style>
</head>
<body>
<div class="slide">
  <div class="backdrop-glow" role="img" aria-label="Soft pink and violet geometric triangle backdrop"></div>

  <h1 class="slide-title">Framework to define lifecycle management processes</h1>
  <div class="header-rule"></div>
  <div class="logo-slot">LOGO HERE</div>

  <div class="mesh-photo" role="img" aria-label="Photo of a steel wire mesh grid"></div>

  <svg class="connectors" width="1200" height="900" viewBox="0 0 1200 900" aria-hidden="true">
    <g stroke="var(--connector)" stroke-width="4" fill="none" stroke-linecap="round" stroke-linejoin="round">
      <line x1="204" y1="278" x2="298" y2="428"/>
      <line x1="204" y1="562" x2="298" y2="428"/>
      <line x1="415" y1="428" x2="496" y2="428"/>
      <polyline points="484,418 497,428 484,438"/>
      <line x1="627" y1="428" x2="736" y2="428"/>
      <polyline points="724,418 737,428 724,438"/>
      <line x1="867" y1="428" x2="948" y2="428"/>
      <polyline points="936,418 949,428 936,438"/>
    </g>
  </svg>

  <div class="stage-box dev" style="left:87px; top:210px;"><span class="dev-label">DEV</span><span class="dev-number">1</span></div>
  <div class="stage-box dev" style="left:87px; top:510px;"><span class="dev-label">DEV</span><span class="dev-number">2</span></div>
  <div class="stage-box qa" style="left:298px; top:370px;">QA</div>
  <div class="stage-box qa" style="left:510px; top:370px;">QA</div>
  <div class="stage-box qa" style="left:750px; top:370px;">QA</div>
  <div class="stage-box qa" style="left:961px; top:370px;">QA</div>

  <footer class="footer">
    <svg class="footer-shapes" width="1200" height="57" viewBox="0 0 1200 57" aria-hidden="true">
      <rect x="0" y="0" width="1200" height="57" fill="var(--footer-dark)"/>
      <polygon points="900,0 1200,0 1200,57 945,57" fill="var(--white)"/>
      <polygon points="916,0 1200,0 1200,57 961,57" fill="var(--footer-light)"/>
    </svg>
    <span class="page-number">Page : 01</span>
    <span class="copyright">Copyright text here</span>
  </footer>
</div>
</body>
</html>
```